TK Stationery - Modern Contemporary

Develop modern template for Letterhead and Stationery (business card, letterhead, envelopes) using the TK Logo and Icon

Colors
0054AA
0677BA
7BADD7
CADEEF
E8F1F8
00AB8E
00BBA5
67D7C9
C6EFE9
E9F9F6
EE7325
F08F49
F5BC92
FAE3D3
FDF4ED
6B429C
8869AF
B7A5CE
E3DAEB
F3F0F8

```html
<!DOCTYPE html>
<html lang="en">
<head>
<meta charset="utf-8">
<title>Talla Kanto Letterhead</title>
<link href="https://fonts.googleapis.com/css2?family=Arimo:wght@400;700&family=Questrial&display=swap" rel="stylesheet">
<style>
  :root{
    --backdrop:#cdcccd;
    --paper:#ffffff;
    --navy:#2a3049;
    --green:#3bb273;
    --text:#555559;
    --ink:#4a4a4e;
  }
  *{margin:0;padding:0;box-sizing:border-box}
  html,body{width:1173px;height:1200px;overflow:hidden;background:var(--backdrop)}
  .letterhead{
    position:absolute;left:230px;top:96px;width:714px;height:1008px;
    background:var(--paper);box-shadow:2px 2px 3px rgba(0,0,0,.35);
    font-family:"Arimo",Arial,sans-serif;color:var(--text);
  }
  .header-art{position:absolute;left:0;top:0;width:714px;height:110px;display:block}
  .brand-name{
    position:absolute;left:0;top:14px;width:714px;text-align:center;
    font-family:"Questrial",sans-serif;font-size:44px;line-height:50px;
    color:var(--paper);letter-spacing:.5px;
  }
  .salutation{
    position:absolute;left:65px;top:309px;
    font-family:"Questrial",sans-serif;font-weight:700;font-size:16.5px;color:var(--text);
    -webkit-text-stroke:.3px var(--text);
  }
  .letter-body{position:absolute;left:63px;top:356px;width:583px}
  .letter-body p{
    font-size:11.4px;line-height:14.7px;text-align:justify;margin-bottom:12.5px;
  }
  .closing{
    position:absolute;left:65px;top:660px;
    font-family:"Questrial",sans-serif;font-size:9px;font-weight:700;color:var(--ink);
    -webkit-text-stroke:.2px var(--ink);
  }
  .signature{
    position:absolute;left:64px;top:702px;width:117px;height:36px;
    background:linear-gradient(90deg,#e9e9ea,#d9d9db);border-radius:3px;
  }
  .footer-rule{position:absolute;left:67px;top:921px;width:579px;height:1px;background:var(--navy)}
  .contact-list{position:absolute;left:67px;top:933px;list-style:none}
  .contact-list li{
    display:flex;align-items:center;height:14.3px;
    font-size:11.7px;color:var(--navy);
  }
  .contact-list svg{width:9px;height:9px;margin-right:8px;flex:none}
  .address{
    position:absolute;right:68px;top:933px;text-align:right;
    font-size:11.7px;line-height:14.3px;color:var(--navy);
  }
</style>
</head>
<body>
<main class="letterhead">
  <svg class="header-art" viewBox="0 0 714 110" aria-hidden="true">
    <path d="M0 0H714V43Q380 108 0 51Z" fill="var(--navy)"/>
    <path d="M164 68Q470 84 714 58V67Q460 104 164 68Z" fill="var(--navy)"/>
    <path d="M0 56Q300 108 570 88Q320 124 0 71Z" fill="var(--green)"/>
  </svg>
  <div class="brand-name">talla kanto</div>

  <h1 class="salutation">Dear Mr. Smith,</h1>

  <section class="letter-body">
    <p>Lorem ipsum dolor sit amet, consectetuer adipiscing elit, sed diam nonmmy nibh euismod tincidunt ut laor eet dolore magna aliquam erat volutpat. Ut wisi enim ad minim veniam, quis nostrud exerci tationmcorper suscipit lobortis nisl ut aliquip ex ea commodo consequat. Duis autem vel eum iriure dolor in hendrerit in vulputate velit esse molestie consequat, vel illum dolore eu feugiat</p>
    <p>Rorem ipsum dolor sit amet, consectetuer adipiscing elit, sed diam nonmmy nibh euismod tincidunt ut laor eet dolore magna aliquam erat volutpat. Ut wisi enim ad minim veniam, quis nostrud exerci tationmcorper suscipit lobortis nisl ut aliquip ex ea commodo consequat. Duis autem vel eum iriure dolor in hendrerit in vulputate velit esse molest</p>
    <p>Dorem ipsum dolor sit amet, consectetuer adipiscing elit, sed diam nonmmy nibh euismod tincidunt ut laor eet dolore magna aliquam erat volutpat. Ut wisi enim ad minim veniam, quis nostrud exerci tationmcorper suscipit lobortis nisl ut aliquip ex ea commodo consequat. Duis autem vel eum iriure dolor in hendrerit in suscipit lobortis nisl ut aliquip ex ea commodo consequat. Duis autem vel eum iriure dolor in hendrerit in vulputate velit esse molestie consequat, vel illum</p>
    <p>Sorem ipsum dolor sit amet, consectetuer adipiscing elit, sed diam nonmmy nibh euismod tincidunt ut laor eet dolore magna aliquam erat volutpat. Ut wisi enim ad minim veniam, quis nostrud exerci tationmcorper suscipit lobortis nisl ut aliquip ex ea commodo consequat. Duis autem vel eum iriure dolor in</p>
  </section>

  <div class="closing">Sincerely,</div>
  <div class="signature" role="img" aria-label="Handwritten signature of the sender"></div>

  <div class="footer-rule"></div>
  <ul class="contact-list">
    <li><svg viewBox="0 0 10 10"><path d="M2 1l2 2-1 1.2c.6 1.2 1.5 2.1 2.8 2.8L7 6l2 2-1.3 1.3C4.5 9 1 5.5.7 2.3Z" fill="var(--green)"/></svg>555-014-2100</li>
    <li><svg viewBox="0 0 10 10"><rect x="0.5" y="2" width="9" height="6.5" fill="var(--green)"/><path d="M.5 2L5 5.8 9.5 2" stroke="#fff" stroke-width="1" fill="none"/></svg>info@tallakanto.com</li>
    <li><svg viewBox="0 0 10 10"><circle cx="5" cy="5" r="4.6" fill="var(--green)"/><path d="M.5 5h9M5 .5c-2 2.5-2 6.5 0 9M5 .5c2 2.5 2 6.5 0 9" stroke="#fff" stroke-width=".8" fill="none"/></svg>www.tallakanto.com</li>
  </ul>
  <address class="address" style="font-style:normal">Your address<br>city<br>state, ZIP 0000</address>
</main>
</body>
</html>
```